RWT Fittings Ltd Business Cards

We need a business card with our business logo. We provide window and door installations on high-rises in west coast British Colombia, Canada.

I would like my business information and details on one side of the card, and the other side the company name with logo

Target Market(s)

General Contractors

Industry/Entity Type

Construction

Contact Information for Business Card

one side i want my company name and logo in the dark theme logo that i provided

Requirements
Must have
• Marco Peltieri, 16045518293, RWTFittings@mailbox-demo.com, 1407-5194 Linden Row Burnaby BC, V5H 2K9, Owner & Manager

```html
<!DOCTYPE html>
<html lang="en">
<head>
<meta charset="utf-8">
<title>RWT Fittings Ltd – Business Cards</title>
<link rel="stylesheet" href="https://fonts.googleapis.com/css2?family=Roboto:wght@400;700&display=swap">
<style>
  :root {
    --backdrop: #202020;
    --band: #1c1c1e;
    --card-grey: #9b9b9b;
    --pattern-light: #a3a3a3;
    --pattern-dark: #8c8c8c;
    --brand-blue: #29a8e0;
    --ink-white: #ffffff;
  }
  * { box-sizing: border-box; margin: 0; padding: 0; }
  html, body {
    width: 1200px; height: 780px; overflow: hidden;
    background: var(--backdrop);
    font-family: "Roboto", Arial, sans-serif;
  }
  .stage {
    position: relative; width: 1200px; height: 780px;
    display: flex; align-items: center; justify-content: center; gap: 50px;
  }
  .card {
    position: relative; width: 525px; height: 300px; overflow: hidden;
    box-shadow: 0 14px 30px rgba(0,0,0,.45);
  }

  /* Front: contact side */
  .card--front { background: var(--card-grey); }
  .brand-band {
    position: absolute; left: 0; top: 0; bottom: 0; width: 100px;
    background: var(--band);
    display: flex; align-items: center; justify-content: center;
  }
  .brand-band__name {
    transform: rotate(-90deg);
    white-space: nowrap;
    color: var(--brand-blue);
    font-weight: 700; font-size: 24px; letter-spacing: 1px;
    display: flex; align-items: center; gap: 10px;
  }
  .brand-band__mark {
    width: 18px; height: 18px; background: var(--brand-blue);
  }
  .contact {
    position: absolute; right: 40px; bottom: 32px;
    text-align: right; color: var(--ink-white);
  }
  .contact__name { font-weight: 700; font-size: 27px; line-height: 1.05; }
  .contact__role { font-size: 14px; margin-top: 2px; }
  .contact__address { font-size: 13px; line-height: 1.35; margin-top: 10px; }
  .contact__line {
    font-size: 13px; margin-top: 6px;
    display: flex; justify-content: flex-end; align-items: center; gap: 8px;
  }
  .contact__line + .contact__line { margin-top: 3px; }
  .contact__icon { width: 12px; height: 12px; fill: var(--ink-white); }
  .accent-bar {
    position: absolute; right: 0; top: 116px;
    width: 26px; height: 46px; background: var(--ink-white);
  }

  /* Back: brand side */
  .card--back { background: var(--card-grey); }
  .pattern-field {
    position: absolute; inset: 0;
    background: linear-gradient(135deg, var(--pattern-light), var(--pattern-dark));
  }
  .back-brand {
    position: absolute; left: 50%; top: 66%;
    transform: translateX(-50%);
    color: var(--ink-white);
    font-weight: 700; font-size: 15px; letter-spacing: 1px;
    white-space: nowrap;
  }
</style>
</head>
<body>
<main class="stage">
  <section class="card card--front" aria-label="Business card front">
    <div class="brand-band">
      <div class="brand-band__name"><span class="brand-band__mark"></span>RWT FITTINGS LTD</div>
    </div>
    <div class="accent-bar"></div>
    <div class="contact">
      <p class="contact__name">Marco Peltieri</p>
      <p class="contact__role">Owner &amp; Manager</p>
      <p class="contact__address">1407-5194 Linden Row<br>Burnaby BC, V5H 2K9</p>
      <p class="contact__line">1 604 551 8293
        <svg class="contact__icon" viewBox="0 0 24 24" aria-hidden="true"><path d="M6.6 10.8a15.1 15.1 0 0 0 6.6 6.6l2.2-2.2c.3-.3.7-.4 1-.2 1.1.4 2.3.6 3.6.6.6 0 1 .4 1 1V20c0 .6-.4 1-1 1C10.6 21 3 13.4 3 4c0-.6.4-1 1-1h3.5c.6 0 1 .4 1 1 0 1.3.2 2.5.6 3.6.1.3 0 .7-.2 1z"/></svg>
      </p>
      <p class="contact__line">RWTFittings@mailbox-demo.com
        <svg class="contact__icon" viewBox="0 0 24 24" aria-hidden="true"><path d="M2 5h20v14H2zm2 2v.5l8 5 8-5V7zm0 2.8V17h16V9.8l-8 5z"/></svg>
      </p>
    </div>
  </section>

  <section class="card card--back" aria-label="Business card back">
    <div class="pattern-field" role="img" aria-label="Repeating pattern of small building marks in light and mid grey"></div>
    <p class="back-brand">RWT FITTINGS LTD</p>
  </section>
</main>
</body>
</html>
```